BildeVOLD buisnesscard

Hey :) I need a modern buisnesscard for my company BildeVOLD
It most have:
Dagligleder og Fotograf: Henrik Audun Strandvik

Mob: +4791264085
Epost: post@bildevold.example
Adresse: Kvernbakken9, 6040 Strandvoll

Facbook and instagram logo with text BildeVOLD

BildeVOLD logo

It Company

```html
<!DOCTYPE html>
<html lang="no">
<head>
<meta charset="utf-8">
<title>BildeVOLD business card</title>
<link href="https://fonts.googleapis.com/css2?family=Roboto:wght@400;500;700&display=swap" rel="stylesheet">
<style>
  :root {
    --backdrop: #3a302c;
    --card: #1c1c1e;
    --card-edge: #111112;
    --ink-light: #b9b9bc;
    --ink-mid: #8e8e92;
    --ink-dark: #2a2a2c;
    --band: #a9a9ad;
    --rule: #5c5c60;
  }
  * { box-sizing: border-box; margin: 0; padding: 0; }
  html, body { width: 1200px; height: 716px; overflow: hidden; }
  body {
    background: var(--backdrop);
    font-family: "Roboto", Arial, sans-serif;
    display: flex;
    align-items: center;
    justify-content: center;
    gap: 60px;
  }
  .card {
    position: relative;
    width: 520px;
    height: 298px;
    background: var(--card);
    border: 1px solid var(--card-edge);
    overflow: hidden;
  }
  /* Back side */
  .card-back { display: flex; align-items: center; justify-content: center; gap: 14px; }
  .card-back .mark-square { width: 34px; height: 34px; background: var(--ink-dark); }
  .card-back .brand { font-size: 46px; font-weight: 700; color: var(--ink-dark); letter-spacing: 0.5px; }

  /* Front side */
  .brand-row {
    position: absolute; left: 34px; top: 34px;
    display: flex; align-items: center; gap: 14px;
  }
  .brand-row .mark-square { width: 30px; height: 30px; background: var(--ink-light); }
  .brand-row .divider { width: 1px; height: 34px; background: var(--ink-light); }
  .brand-row .brand { font-size: 34px; font-weight: 700; color: var(--ink-light); }

  .person { position: absolute; left: 34px; top: 124px; }
  .person .name { font-size: 15px; font-weight: 700; color: var(--ink-light); }
  .person .title { font-size: 11px; color: var(--ink-mid); margin-top: 4px; }
  .website { position: absolute; left: 34px; top: 180px; font-size: 11px; color: var(--ink-mid); }

  .contacts { position: absolute; left: 276px; top: 168px; width: 214px; color: var(--ink-light); font-size: 12px; }
  .contacts .row { display: flex; align-items: center; gap: 8px; height: 18px; white-space: nowrap; }
  .contacts .social .icon-square { width: 10px; height: 10px; background: var(--ink-light); }
  .contacts .rule { height: 1px; background: var(--rule); margin: 10px 0 8px; }
  .contacts svg { width: 12px; height: 12px; flex: none; fill: none; stroke: var(--ink-light); stroke-width: 1.4; }

  .band { position: absolute; left: 0; right: 0; bottom: 0; height: 12px; background: var(--band); }
</style>
</head>
<body>
  <section class="card card-back" aria-label="Card back">
    <span class="mark-square"></span>
    <span class="brand">BildeVOLD</span>
  </section>

  <section class="card card-front" aria-label="Card front">
    <div class="brand-row">
      <span class="mark-square"></span>
      <span class="divider"></span>
      <span class="brand">BildeVOLD</span>
    </div>

    <div class="person">
      <p class="name">Henrik Audun Strandvik</p>
      <p class="title">Dagligleder &amp; Fotograf</p>
    </div>
    <p class="website">www.bildevold.example</p>

    <div class="contacts">
      <div class="row social"><span class="icon-square"></span><span>/BildeVOLD</span></div>
      <div class="rule"></div>
      <div class="row">
        <svg viewBox="0 0 12 12"><rect x="3" y="1" width="6" height="10" rx="1"/><line x1="5" y1="9" x2="7" y2="9"/></svg>
        <span>+4791264085</span>
      </div>
      <div class="row">
        <svg viewBox="0 0 12 12"><rect x="1" y="2.5" width="10" height="7"/><polyline points="1,2.5 6,6.5 11,2.5"/></svg>
        <span>post@bildevold.example</span>
      </div>
      <div class="row">
        <svg viewBox="0 0 12 12"><path d="M6 11 C3 7.5 2.5 6 2.5 4.5 A3.5 3.5 0 0 1 9.5 4.5 C9.5 6 9 7.5 6 11Z"/><circle cx="6" cy="4.5" r="1.2"/></svg>
        <span>Kvernbakken9, 6040 Strandvoll</span>
      </div>
    </div>

    <div class="band"></div>
  </section>
</body>
</html>
```